verdant terraces simple classy business card design

my name is colin barrow and I run a gardening business aimed at high class verdant terraces. the business name is verdant terraces and our logo was designed on pixel harbour .My clientel are anything from residential homes to businesses. I take pride in my work and know that I offer a service like no other in my area.
The business card will be used to represent my business and I want it to be not only rememberable, but simplistic and modern. Eye catching too. Of course I would like it relatable to gardening and appealing to the correct clientel - those being garden enthusiasts, prestigious homes and businesses that are after top of the line gardening services like no other on the market.
I am not a typical lawn mowing business so I don't want a typical card design that represents that. The gardens I work with are generally million dollar properties with owners who are very garden proud looking for upkeep and guidance from me along with sometimes whole new garden designs. I want the business cards to show to my clients that I take pride, as they do, in their garden. And I want them to know from my card that I am a professional, qualified horticulturist offering them a top of the line service for life. I want them to refer my business on. I want them to look at my business card and see class and professionalism in a modern unique bold way.
The card should be simple with the possibility of the logo on the front being embossed/debossed and my details on the back the card should have a organic garden feel it's very important to me that it is absolutely perfect
I am also very open to ideas and suggestions so look forward to seeing the designs. the business logo has been supplied with this project and I want the card to be double sided

Contact info is
Colin Barrow - Managing Director / Horticulturist
Phone : 0481 526 704
Email: colinbarrow@verdantterraces.example.au

Target Market(s)

high class gardens residential and commercial

Industry/Entity Type

Gardener

Contact Information for Business Card

Contact info is
Phone : 0481 526 704

PLEASE MAKE CARD DOUBLE SIDED

Requirements
Must have
• organic simple classy modern feel
• must flow with the current logo that has been supplied with this project
• Double sided
• Must explain in a simple way that I deal with high end gardens and I'm a qualified horticulturist
Nice to have
• embossed debossed logo
Should not have
• shouldn't be to busy or cheap looking

```html
<!DOCTYPE html>
<html lang="en">
<head>
<meta charset="utf-8">
<title>Verdant Terraces – Business Card</title>
<link rel="stylesheet" href="https://fonts.googleapis.com/css2?family=Cinzel:wght@400&family=Tinos:wght@700&family=Open+Sans:wght@400&display=swap">
<style>
  :root {
    --stage: #000000;
    --paper: #f3f3f3;
    --leaf: #5f9a50;
    --leaf-deep: #4f8842;
    --leaf-shade: #548d46;
    --ink: #2a2a2a;
    --white: #ffffff;
  }
  * { box-sizing: border-box; margin: 0; padding: 0; }
  html, body { width: 1200px; height: 900px; overflow: hidden; background: var(--stage); }
  .stage { position: relative; width: 1200px; height: 900px; }

  .card { position: absolute; top: 200px; width: 310px; height: 502px; overflow: hidden; }
  .card--back { left: 265px; background: var(--paper); border-radius: 62px 0 62px 0; }
  .card--front { left: 641px; width: 309px; background: var(--leaf); border-radius: 0 62px 0 62px; }

  .wordmark { position: absolute; left: 0; right: 0; text-align: center;
    font-family: "Cinzel", "Times New Roman", serif; font-weight: 400; }
  .wordmark__dot { display: block; margin: 0 auto 10px; border-radius: 50%; }
  .wordmark__text { display: block; font-size: 29px; line-height: 1.1; letter-spacing: 1px; }

  .card--back .wordmark { top: 113px; color: var(--leaf); }
  .card--back .wordmark__dot { width: 62px; height: 62px; background: var(--leaf); }
  .card--front .wordmark { top: 190px; color: var(--white); }
  .card--front .wordmark__dot { width: 62px; height: 62px; background: var(--white); }

  .contact { position: absolute; left: 35px; top: 297px; color: var(--ink);
    font-family: "Open Sans", Arial, sans-serif; font-size: 13px; line-height: 18.5px; }
  .contact__name { font-family: "Tinos", "Times New Roman", serif; font-weight: 700;
    font-size: 19px; color: var(--leaf); line-height: 22px; }
  .contact__role { margin-bottom: 10px; }
  .contact__line { display: flex; align-items: center; gap: 5px; white-space: nowrap; }
  .contact__line svg { width: 9px; height: 9px; flex: none; fill: var(--leaf); }
  .contact__address { margin-top: 8px; }

  .foliage { position: absolute; }
  .card--back .foliage { right: 0; bottom: 0; width: 140px; height: 110px;
    border-radius: 100% 0 0 0;
    background: radial-gradient(circle at 100% 100%, var(--leaf-deep) 0%, var(--leaf) 60%, rgba(95,154,80,0.75) 100%); }
  .card--front .foliage { left: 0; bottom: 0; width: 135px; height: 118px;
    border-radius: 0 100% 0 0;
    background: radial-gradient(circle at 0% 100%, var(--leaf-shade) 0%, var(--leaf-deep) 55%, var(--leaf) 100%); }
</style>
</head>
<body>
<main class="stage">
  <section class="card card--back" aria-label="Business card, details side">
    <div class="wordmark">
      <span class="wordmark__dot"></span>
      <span class="wordmark__text">Verdant</span>
      <span class="wordmark__text">Terraces</span>
    </div>
    <div class="contact">
      <p class="contact__name">Colin Barrow</p>
      <p class="contact__role">Managing Director</p>
      <p class="contact__line">
        <svg viewBox="0 0 10 10"><path d="M2 0.5 L3.6 2.6 L2.7 3.6 C3.3 4.9 4.9 6.6 6.4 7.3 L7.4 6.4 L9.5 8 L8.4 9.5 C4.6 9.2 0.8 5.4 0.5 1.6 Z"/></svg>
        0481 526 704
      </p>
      <p class="contact__line">
        <svg viewBox="0 0 10 10"><path d="M0.5 2 H9.5 V8 H0.5 Z M1.2 2.6 L5 5.4 L8.8 2.6 Z" fill-rule="evenodd"/></svg>
        colinbarrow@verdantterraces.example.au
      </p>
      <p class="contact__line">
        <svg viewBox="0 0 10 10"><circle cx="5" cy="5" r="4.3" fill="none" stroke="#5f9a50" stroke-width="0.9"/><path d="M0.7 5 H9.3 M5 0.7 C2.5 3 2.5 7 5 9.3 M5 0.7 C7.5 3 7.5 7 5 9.3" fill="none" stroke="#5f9a50" stroke-width="0.8"/></svg>
        www.verdantterraces.example.au
      </p>
      <p class="contact__address">27 Fernleaf Rise, Elmvale<br>Australia, 4017.</p>
    </div>
    <div class="foliage" role="img" aria-label="Cluster of green leaves rising from the bottom corner"></div>
  </section>

  <section class="card card--front" aria-label="Business card, logo side">
    <div class="wordmark">
      <span class="wordmark__dot"></span>
      <span class="wordmark__text">Verdant</span>
      <span class="wordmark__text">Terraces</span>
    </div>
    <div class="foliage" role="img" aria-label="Debossed leaf cluster in the bottom corner"></div>
  </section>
</main>
</body>
</html>
```